Business Card Design for BrightvaleMedia.com

--I need a business card design for my company BrightvaleMedia.com

I have attached my logo...I want the brightvale media logo on the front of the business card, and then I want The Quillstone Chief on the back of it with my information.

I would like to see a light colored background as well as a dark colored background

FRONT:
BRIGHTVALE MEDIA LOGO
248 N. Larkmoor
3rd Floor
San Diego CA 92173
www.BrightvaleMedia.com

Advanced Website & App Development
Websites, Apps, Online Voucher Systems

Leading Edge Marketing Services
SMS, VB, SMM, SEM,

BACK:
QUILLSTONE CHIEF LOGO
Dorian Pelletta
The Quillstone Chief
Call Or Text: 619-555-0148
Dorian@QuillstoneChief.example
www.QuillstoneChief.example

Target Market(s)

small business owners

Industry/Entity Type

Business Consultant

Contact Information for Business Card

FRONT:
BRIGHTVALE MEDIA LOGO
248 N. Larkmoor
3rd Floor
San Diego CA 92173
www.BrightvaleMedia.com

SMS, VB, SMM, SEM,

BACK:
QUILLSTONE CHIEF LOGO
Dorian Pelletta
The Quillstone Chief
Dorian@QuillstoneChief.example
www.QuillstoneChief.example

Requirements
Must have
• add this quote on it somewhere, anywhere,preferrably on back
• "The Fastest Way To Success Is To Take Action”
• — Dorian Pelletta, Quillstone Chief
Nice to have
• open
Should not have
• red

```html
<!DOCTYPE html>
<html lang="en">
<head>
<meta charset="utf-8">
<title>Brightvale Media – Business Cards</title>
<link href="https://fonts.googleapis.com/css2?family=Montserrat:wght@400;500;600;700&display=swap" rel="stylesheet">
<style>
  :root {
    --stage: #2e2f31;
    --brand-blue: #1b73ae;
    --deep-blue: #1565a0;
    --steel-grey: #77787b;
    --soft-grey: #8a8b8e;
    --paper: #ffffff;
    --ink: #5a5b5e;
  }
  * { box-sizing: border-box; margin: 0; padding: 0; }
  html, body {
    width: 1200px; height: 900px; overflow: hidden;
    background: var(--stage);
    font-family: "Montserrat", Arial, sans-serif;
  }
  .stage { position: relative; width: 1200px; height: 900px; }
  .card {
    position: absolute; left: 300px;
    width: 600px; height: 343px;
    border-radius: 22px; overflow: hidden;
    box-shadow: 0 12px 30px rgba(0,0,0,.45);
  }
  .card-decor { position: absolute; inset: 0; width: 100%; height: 100%; }

  /* Front */
  .card-front { top: 70px; background: var(--brand-blue); color: var(--paper); }
  .front-name {
    position: absolute; left: 48px; top: 58px;
    font-weight: 500; font-size: 36px; letter-spacing: 3px; line-height: 1.15;
    color: var(--paper);
  }
  .front-address {
    position: absolute; right: 82px; top: 78px; text-align: right;
    font-style: normal; font-size: 13px; line-height: 1.4;
  }
  .front-address .web { margin-top: 18px; }
  .front-services { position: absolute; left: 48px; bottom: 36px; font-size: 14px; line-height: 1.4; }
  .front-services .strong { font-weight: 700; }

  /* Back */
  .card-back { top: 487px; background: var(--paper); }
  .back-name {
    position: absolute; left: 78px; top: 50px;
    font-weight: 600; font-size: 38px; letter-spacing: 3px; line-height: 1;
    color: var(--brand-blue);
  }
  .back-person { position: absolute; right: 60px; top: 126px; text-align: right; }
  .back-person .name { font-weight: 700; font-size: 22px; color: var(--deep-blue); }
  .back-person .title { font-size: 10px; color: var(--ink); letter-spacing: 1px; }
  .back-rule { position: absolute; left: 110px; right: 60px; top: 178px; height: 1.5px; background: var(--soft-grey); }
  .back-contact { position: absolute; left: 110px; top: 208px; list-style: none; font-size: 14px; color: var(--ink); }
  .back-contact li { display: flex; align-items: center; gap: 8px; line-height: 1.4; }
  .back-contact svg { width: 11px; height: 11px; fill: var(--brand-blue); flex: none; }
  .back-contact .hl { color: var(--brand-blue); font-weight: 600; }
  .back-quote {
    position: absolute; left: 110px; bottom: 30px;
    font-size: 16px; letter-spacing: 1px; text-transform: uppercase; color: var(--ink);
  }
</style>
</head>
<body>
<main class="stage">

  <section class="card card-front" aria-label="Front of card">
    <svg class="card-decor" viewBox="0 0 600 343" preserveAspectRatio="none" aria-hidden="true">
      <polygon points="548,0 600,0 600,118 590,118 548,80" fill="var(--steel-grey)"/>
      <polygon points="560,118 600,118 600,343 548,343 548,130" fill="var(--paper)"/>
    </svg>
    <div class="front-name">BRIGHTVALE<br>MEDIA</div>
    <address class="front-address">
      248 N. Larkmoor<br>3rd Floor
      <div class="web">San Diego CA 92173<br>www.BrightvaleMedia.com</div>
    </address>
    <div class="front-services">
      Advanced Website &amp; App Development<br>
      Websites, Apps, Online Voucher Systems<br>
      <span class="strong">LEADING EDGE MARKETING SERVICES<br>SMS, VB, SMM, SEM,</span>
    </div>
  </section>

  <section class="card card-back" aria-label="Back of card">
    <svg class="card-decor" viewBox="0 0 600 343" preserveAspectRatio="none" aria-hidden="true">
      <polygon points="0,0 52,0 52,192 90,232 0,232" fill="var(--brand-blue)"/>
      <polygon points="0,232 90,232 90,343 0,343" fill="var(--steel-grey)"/>
      <polygon points="52,232 90,232 90,343 60,343" fill="var(--soft-grey)"/>
      <polygon points="0,232 52,232 52,343 0,343" fill="var(--paper)"/>
      <polygon points="560,128 600,128 600,150" fill="var(--brand-blue)"/>
      <polygon points="572,150 600,150 600,178" fill="var(--steel-grey)"/>
    </svg>
    <div class="back-name">QUILLSTONE CHIEF</div>
    <div class="back-person">
      <div class="name">Dorian Pelletta</div>
      <div class="title">CEO</div>
    </div>
    <div class="back-rule"></div>
    <ul class="back-contact">
      <li><svg viewBox="0 0 10 10"><path d="M2 0 L4 2.5 L3 4 Q4 6 6 7 L7.5 6 L10 8 L8.5 10 Q3 9.5 0 2 Z"/></svg><span>619-555-0148</span></li>
      <li><svg viewBox="0 0 10 10"><path d="M0 2 H10 V8 H0 Z M1 3 V7 H9 V3 L5 5.5 Z" fill-rule="evenodd"/></svg><span>Dorian@QuillstoneChief.example</span></li>
      <li><svg viewBox="0 0 10 10"><circle cx="5" cy="5" r="5"/></svg><span>www.<span class="hl">QuillstoneChief</span>.example</span></li>
    </ul>
    <p class="back-quote">The fastest way to success is to take action</p>
  </section>

</main>
</body>
</html>
```